Executive Business Card for Healthcare Company [Need Today]

I need a business card design for a healthcare company. The only branding the company has thus far is a logo. The cards will be utilized by company executives. The design I envision will be vibrant and appealing but with a corporate feel. They shouldn't be too casual or playful. I would like to complete this project TODAY if possible.

Target Market(s)

Healthcare vendors, other executives in healthcare and pharmaceuticals

Industry/Entity Type

Pharmaceutical

Contact Information for Business Card

See attachment

Font styles to use
Serif
Sans Serif

Colors

Designer to choose colors to be used in the design.

```html
<!DOCTYPE html>
<html lang="en">
<head>
<meta charset="utf-8">
<title>Lumera Therapeutics – Executive Business Card</title>
<link href="https://fonts.googleapis.com/css2?family=Lato:wght@300;400;700&display=swap" rel="stylesheet">
<style>
  :root {
    --bg: #e9eaec;
    --teal: #25afc4;
    --green: #4db38c;
    --name-teal: #2a9fb3;
    --ink: #3c3f44;
    --muted: #6b6f75;
    --paper: #ffffff;
    --fold-grey: #7d8085;
  }
  * { margin: 0; padding: 0; box-sizing: border-box; }
  html, body { width: 1200px; height: 726px; overflow: hidden; }
  body {
    background: var(--bg);
    font-family: "Lato", sans-serif;
    position: relative;
  }
  .card {
    position: absolute;
    width: 520px;
    height: 297px;
    border-radius: 3px;
    overflow: hidden;
    box-shadow: 0 6px 18px rgba(0,0,0,0.12);
  }
  /* Front */
  .card-front {
    left: 45px;
    top: 214px;
    background: linear-gradient(160deg, var(--teal) 0%, var(--green) 100%);
    color: var(--paper);
  }
  .front-brand {
    position: absolute;
    left: 0; right: 0;
    top: 108px;
    display: flex;
    align-items: center;
    justify-content: center;
    gap: 18px;
  }
  .brand-dot {
    flex: none;
    width: 54px; height: 54px;
    border: 2px solid var(--paper);
    border-radius: 50%;
  }
  .brand-name {
    font-size: 30px;
    font-weight: 300;
    letter-spacing: 1px;
    white-space: nowrap;
  }
  .front-web {
    position: absolute;
    left: 0; right: 0;
    bottom: 38px;
    text-align: center;
    font-size: 13px;
    font-weight: 300;
    letter-spacing: 4px;
  }
  /* Back */
  .card-back {
    left: 635px;
    top: 214px;
    background: var(--paper);
  }
  .back-panel { position: absolute; inset: 0; }
  .back-brand {
    position: absolute;
    left: 440px;
    top: 150px;
    display: flex;
    align-items: center;
    gap: 12px;
    color: var(--paper);
    transform: translate(-50%, -50%) rotate(-90deg);
  }
  .back-brand .brand-dot { width: 40px; height: 40px; }
  .back-brand .brand-name { font-size: 18px; }
  .person {
    position: absolute;
    left: 34px;
    top: 40px;
  }
  .person-name {
    font-size: 24px;
    font-weight: 400;
    color: var(--name-teal);
  }
  .person-title {
    margin-top: 4px;
    margin-left: 14px;
    font-size: 11px;
    color: var(--muted);
  }
  .contacts {
    position: absolute;
    left: 34px;
    bottom: 34px;
    list-style: none;
    font-size: 14px;
    color: var(--ink);
    line-height: 20px;
  }
  .contacts li { display: flex; align-items: center; gap: 8px; }
  .contacts .icon { width: 12px; height: 12px; flex: none; }
  .contacts .plain { padding-left: 20px; }
</style>
</head>
<body>

<section class="card card-front">
  <div class="front-brand">
    <span class="brand-dot"></span>
    <span class="brand-name">Lumera Therapeutics</span>
  </div>
  <p class="front-web">www.lumerarx.com</p>
</section>

<section class="card card-back">
  <svg class="back-panel" width="520" height="297" viewBox="0 0 520 297" aria-hidden="true">
    <defs>
      <linearGradient id="panelFill" x1="0" y1="1" x2="1" y2="0">
        <stop offset="0" stop-color="#25afc4"/>
        <stop offset="1" stop-color="#4db38c"/>
      </linearGradient>
    </defs>
    <path d="M318,0 C290,90 362,170 300,297 L520,297 L520,0 Z" fill="#7d8085"/>
    <path d="M330,0 C302,90 374,170 312,297 L520,297 L520,0 Z" fill="url(#panelFill)"/>
  </svg>

  <div class="back-brand">
    <span class="brand-dot"></span>
    <span class="brand-name">Lumera Therapeutics</span>
  </div>

  <div class="person">
    <h1 class="person-name">Daniel Hale</h1>
    <p class="person-title">Senior Director of Marketing</p>
  </div>

  <ul class="contacts">
    <li>
      <svg class="icon" viewBox="0 0 12 12" aria-hidden="true"><rect width="12" height="12" rx="2" fill="#2a9fb3"/><path d="M3 3.5 L5 3 L5.6 5 L4.6 5.6 Q5.5 7.3 6.4 7.4 L7 6.4 L9 7 L8.5 9 Q4 9 3 3.5Z" fill="#fff"/></svg>
      555-210-4837
    </li>
    <li>
      <svg class="icon" viewBox="0 0 12 12" aria-hidden="true"><rect width="12" height="12" rx="2" fill="#2a9fb3"/><rect x="4" y="2" width="4" height="8" rx="1" fill="#fff"/></svg>
      555-318-2964
    </li>
    <li>
      <svg class="icon" viewBox="0 0 12 12" aria-hidden="true"><circle cx="6" cy="6" r="6" fill="#2a9fb3"/><path d="M1 6 H11 M6 1 Q3 6 6 11 M6 1 Q9 6 6 11" stroke="#fff" stroke-width="0.8" fill="none"/></svg>
      dhale@lumerarx.com
    </li>
    <li class="plain">118 Elm Park Avenue</li>
    <li class="plain">Riverton, GA 30012</li>
  </ul>
</section>

</body>
</html>
```